New Dynamic Design Based on Other Site

We need a new website designed where the front page is VERY SEO Friendly. The front page should almost follow the same SEO principles that are on RankLoomPress.com. The inner pages need to follow the same exact video animations that occur on vollq.com. I'd like to keep our "marbletons" theme throughout the new design but we will provide all of the content but I want someone to design something SEO friendly, new blog theme, and actual inner pages that are dynamic and based on those short videos.

Check attached file for company name and site that we currently have. Feel free to pull the content from that site and re-use it and also leave placeholders for the rest of them.

PLEASE NO USE OF STOCK IMAGES. Use a designer or an illustrator to create the various images.

Please make sure the front page is SEO friendly! Make sure you familiarize yourself with the quorvix algorithm for SEO. Content above the fold H1 Tags Very mobile friendly Minimal javascript and animations Basically a quality static page with optimized content

Target Market(s)

call center companies, anything call related

Industry/Entity Type

Telecommunications

Number of Pages Required

4 page

Font styles to use
Sans Serif

Colors
33a6d7
85cae6
0792cd
0255a3
cee9f5
ecf7fb
ffffff

Requirements
Must have
• places for video animations
• dynamic functionality
• SEO friendly (front page)
Should not have
• should not look like a template. needs to be unique

```html
<!DOCTYPE html>
<html lang="en">
<head>
<meta charset="utf-8">
<title>Callvera — Call Center Quality Assurance Agency</title>
<link rel="stylesheet" href="https://fonts.googleapis.com/css2?family=Open+Sans:wght@400;600;700&display=swap">
<style>
:root{
  --sky:#33a6d7;--sky-light:#85cae6;--azure:#0792cd;--navy:#0255a3;
  --ice:#cee9f5;--mist:#ecf7fb;--white:#fff;--ink:#333;--muted:#555;--rule:#e3e3e3;
}
*{box-sizing:border-box;margin:0;padding:0}
html,body{width:1200px;height:3340px;overflow:hidden}
body{font-family:'Open Sans',sans-serif;color:var(--ink);background:var(--white);position:relative}
a{color:inherit;text-decoration:none}
.section{position:absolute;left:0;width:1200px}

/* header */
.site-header{top:0;height:156px}
.topbar{position:absolute;right:76px;top:20px;display:flex;gap:28px;font-size:15px;color:var(--navy);font-weight:600}
.topbar span{display:flex;align-items:center;gap:8px}
.brand{position:absolute;left:72px;top:40px;display:flex;align-items:center;gap:10px}
.brand-dot{width:58px;height:58px;border-radius:50%;background:var(--azure)}
.brand-name{font-size:30px;font-weight:700;color:var(--navy)}
.main-nav{position:absolute;right:76px;top:90px;display:flex;align-items:center;gap:38px;font-size:13px;font-weight:600;letter-spacing:.5px}
.btn-login{background:var(--azure);color:#fff;padding:12px 26px;border-radius:3px}

/* hero */
.hero{top:156px;height:412px;background:linear-gradient(135deg,#1a7fd0,#0a5fb3 60%,#0a66bb)}
.hero-copy{position:absolute;left:76px;top:130px;color:#fff}
.hero-copy .eyebrow{font-size:29px;font-weight:400;letter-spacing:.5px}
.hero-copy h1{font-size:44px;font-weight:400;line-height:1.15;margin-top:6px}
.hero-art{position:absolute;left:660px;top:20px;width:440px;height:380px;border-radius:50%;background:radial-gradient(circle,#7ec5ea,#2a86cf 70%,transparent 72%)}
.hero-dots{position:absolute;left:576px;top:378px;display:flex;gap:8px}
.hero-dots i{width:9px;height:9px;border-radius:50%;background:#fff}
.hero-dots i:first-child{background:var(--sky-light)}

/* services */
.services{top:568px;height:367px;border-bottom:1px solid var(--rule)}
.section-title{text-align:center;font-size:25px;font-weight:600;letter-spacing:.5px;color:var(--ink)}
.services .section-title{margin-top:44px}
.service-list{position:absolute;top:112px;left:72px;display:flex;gap:44px}
.service{display:flex;width:336px;gap:20px}
.service-icon{flex:none;width:80px;height:80px;border-radius:50%;background:var(--azure);display:flex;align-items:center;justify-content:center}
.service h3{font-size:19px;font-weight:400;color:var(--navy)}
.service p{font-size:14px;line-height:1.6;color:var(--muted);margin-top:6px}
.pager{position:absolute;left:585px;top:308px;display:flex;gap:8px}
.pager i{width:11px;height:11px;border-radius:50%;background:#ccc}
.pager i:first-child{background:var(--navy)}

/* about */
.about{top:935px;height:545px;border-bottom:1px solid var(--rule)}
.about-photo{position:absolute;left:76px;top:68px;width:420px;height:402px;background:linear-gradient(160deg,#d9dde2,#8d96a1)}
.about-copy{position:absolute;left:523px;top:68px;width:600px}
.about-copy h2{font-size:26px;font-weight:400;color:var(--navy)}
.about-copy p{font-size:14.5px;line-height:1.72;color:var(--muted);margin-top:12px}
.btn-outline{display:inline-block;border:2px solid var(--azure);color:var(--azure);font-size:16px;padding:12px 40px;margin-top:30px}

/* system */
.system{top:1480px;height:612px}
.system .section-title{margin-top:44px}
.tabs{position:absolute;left:447px;top:103px;display:flex}
.tab{width:150px;height:48px;display:flex;align-items:center;justify-content:center;font-size:12px;font-weight:600;letter-spacing:.3px}
.tab-active{border:1px solid var(--rule);border-bottom:none;color:var(--azure);background:#fff}
.tab-alt{background:var(--sky);color:#fff;margin-left:10px;height:46px}
.system-panel{position:absolute;left:76px;top:150px;width:1050px;height:400px;border:1px solid var(--rule)}
.feature{position:absolute;top:40px;width:480px;text-align:center}
.feature-media{height:208px}
.feature h3{font-size:19px;font-weight:400;color:var(--navy);margin-top:22px}
.feature p{font-size:13.5px;line-height:1.6;color:var(--muted);margin:8px 20px 0}

/* testimonial */
.testimonial{top:2092px;height:252px;background:var(--navy);color:#fff}
.counter{position:absolute;left:60px;top:56px;width:140px;text-align:center}
.counter strong{font-size:30px;font-weight:600}
.counter span{display:block;font-size:12px;letter-spacing:.5px;line-height:1.6;margin-top:6px}
.arrows{position:absolute;left:136px;top:168px;display:flex;gap:12px}
.quote{position:absolute;left:300px;top:72px;width:600px;font-size:13.5px;line-height:1.75}
.author-art{position:absolute;left:960px;top:36px;width:140px;height:150px;border-radius:50%;background:radial-gradient(circle,#f3d94b,#c9a52a)}
.author{position:absolute;left:930px;top:200px;width:200px;text-align:center;font-size:13px}
.author strong{display:block;font-weight:700}

/* why */
.why{top:2344px;height:441px;background:var(--sky);color:#fff}
.why h2,.video h2{font-size:25px;font-weight:600;letter-spacing:.5px}
.why-copy{position:absolute;left:76px;top:50px;width:440px}
.why-copy p{font-size:14.5px;line-height:1.75;margin-top:18px}
.btn-light{display:inline-block;border:2px solid #fff;color:#fff;font-size:16px;padding:11px 38px;margin-top:28px}
.video{position:absolute;left:614px;top:50px}
.video-frame{width:512px;height:285px;margin-top:18px;border:3px solid #e5e5e5;background:radial-gradient(circle at 40% 50%,#a5a5a5,#8a8a8a);position:relative}
.play{position:absolute;left:205px;top:100px}

/* cta */
.cta{top:2785px;height:420px;background:var(--azure);color:#fff}
.cta-brand{position:absolute;left:76px;top:56px;display:flex;align-items:center;gap:10px}
.cta-brand .brand-dot{background:#fff;width:44px;height:44px}
.cta-brand .brand-name{color:#fff;font-size:26px}
.cta-copy{position:absolute;left:256px;top:50px;width:870px}
.cta-copy h2{font-size:22px;font-weight:600;letter-spacing:.5px}
.cta-copy p{font-size:14.5px;line-height:1.75;margin-top:14px}
.cta-copy .btn-light{margin-top:22px;padding:10px 34px}
.contact-row{position:absolute;left:100px;top:320px;display:flex;width:1020px;justify-content:space-between;font-size:16px;font-weight:600}
.contact-row span{display:flex;align-items:center;gap:18px}

/* footer */
.site-footer{top:3205px;height:135px;background:var(--navy);color:#fff}
.footer-nav{position:absolute;left:76px;top:34px;display:flex;gap:28px;font-size:12px}
.copyright{position:absolute;left:76px;top:66px;font-size:11px;line-height:1.5}
.social{position:absolute;right:76px;top:60px;display:flex;gap:18px}
.social i{width:20px;height:20px;border-radius:50%;background:#fff}
</style>
</head>
<body>

<header class="section site-header">
  <div class="topbar">
    <span><svg width="14" height="14" viewBox="0 0 24 24"><path fill="currentColor" d="M6.6 10.8a15 15 0 0 0 6.6 6.6l2.2-2.2c.3-.3.7-.4 1-.2 1.1.4 2.3.6 3.6.6.6 0 1 .4 1 1V20c0 .6-.4 1-1 1A17 17 0 0 1 3 4c0-.6.4-1 1-1h3.5c.6 0 1 .4 1 1 0 1.3.2 2.5.6 3.6.1.3 0 .7-.2 1z"/></svg>855.410.2286</span>
    <span><svg width="15" height="12" viewBox="0 0 24 18"><path fill="currentColor" d="M0 0h24v18H0zM2 2v1l10 7 10-7V2z"/></svg>hello@callvera.com</span>
  </div>
  <a class="brand" href="#"><span class="brand-dot"></span><span class="brand-name">Callvera</span></a>
  <nav class="main-nav">
    <a href="#">HOME</a><a href="#">WHO WE ARE</a><a href="#">SERVICES</a><a href="#">BLOG</a><a href="#">CONTACT</a>
    <a class="btn-login" href="#">&#9679; LOG IN</a>
  </nav>
</header>

<section class="section hero">
  <div class="hero-copy">
    <p class="eyebrow">WE ARE ACALL CENTER</p>
    <h1>QUALITY ASSURANCE<br>AGENCY</h1>
  </div>
  <div class="hero-art" role="img" aria-label="Illustration of a call center agent with headset surrounded by communication icons"></div>
  <div class="hero-dots"><i></i><i></i><i></i></div>
</section>

<section class="section services">
  <h2 class="section-title">CALL CENTER QA SERVICES</h2>
  <div class="service-list">
    <div class="service">
      <div class="service-icon"><svg width="34" height="30" viewBox="0 0 34 30"><ellipse cx="15" cy="12" rx="14" ry="10" fill="#fff"/><path d="M6 18l-3 9 10-6z" fill="#fff"/></svg></div>
      <div><h3>Call Center Quality Control</h3><p>Boost your revenue and improve customer experience by identifying key behaviors and procedures that drive sales.</p></div>
    </div>
    <div class="service">
      <div class="service-icon"><svg width="30" height="26" viewBox="0 0 30 26"><path d="M2 0v24h28" stroke="#fff" stroke-width="2" fill="none"/><rect x="7" y="12" width="4" height="10" fill="#fff"/><rect x="14" y="6" width="4" height="16" fill="#fff"/><rect x="21" y="9" width="4" height="13" fill="#fff"/></svg></div>
      <div><h3>Performance Analysis</h3><p>Are your agents interacting with your clients in a way that is reflective of your brand identity? Effective agent performance monitoring..</p></div>
    </div>
    <div class="service">
      <div class="service-icon"><svg width="30" height="28" viewBox="0 0 30 28"><rect x="1" y="12" width="6" height="15" fill="#fff"/><path d="M9 12l6-11c3 0 4 2 3 5l-1 4h9c2 0 3 2 2 4l-3 10c-1 2-2 3-4 3H9z" fill="#fff"/></svg></div>
      <div><h3>Business Process Verification</h3><p>Because higher quality touch points lead to loyal customers, and loyal customers result in repeat purchases..</p></div>
    </div>
  </div>
  <div class="pager"><i></i><i></i></div>
</section>

<section class="section about">
  <div class="about-photo" role="img" aria-label="Photo of smiling call center agents wearing headsets"></div>
  <div class="about-copy">
    <h2>Top Rated Call Center Quality Assurance Agency</h2>
    <p>So why use Callvera's call center quality assurance services to evaluate your customer to agent interactions? If you've ever counted on Vocaly to look up the nearest Thai restaurant or identify the fastest route to the supermarket, you already know that voice recognition software is years away from being as accurate as we would like it to be. Although this provides cheap entertainment for menial tasks, your business's reputation is no laughing matter.</p>
    <p>At Callvera, we avoid this technology gap by using our prove call center QA process which uses real people to listen and evaluate your calls, while combining transcription and keyword flagging to bring you the best of both worlds using a cost effective and detail oriented QA call center monitoring approach.</p>
    <a class="btn-outline" href="#">Learn More</a>
  </div>
</section>

<section class="section system">
  <h2 class="section-title">SYSTEM DETAILS</h2>
  <div class="tabs"><div class="tab tab-active">ACCURACY</div><div class="tab tab-alt">SYSTEM FEATURES</div></div>
  <div class="system-panel">
    <div class="feature" style="left:28px">
      <div class="feature-media" role="img" aria-label="Screenshot of the calibration scoring table" style="background:linear-gradient(180deg,#f0f0f0 0 18%,#3d5566 18% 27%,#f6f3d8 27% 100%)"></div>
      <h3>Calibration</h3>
      <p>This process utilizes minimal client involvement to ensure internal reviewers are calibrated against the "gold" standard within the client's organization.</p>
    </div>
    <div class="feature" style="left:540px">
      <div class="feature-media" role="img" aria-label="Diagram of the agent notification workflow" style="background:linear-gradient(135deg,#4fb0e0,#2c8fcc)"></div>
      <h3>Notification Process</h3>
      <p>This key process is used to identify and manage agents who fall below the fail threshold or as otherwise indicated by the client. Quickly get access to the calls that need your attention ..</p>
    </div>
  </div>
</section>

<section class="section testimonial">
  <div class="counter"><strong>20,736,477</strong><span>MINUTES REVIEWED, AND COUNTING...</span></div>
  <div class="arrows"><svg width="44" height="22" viewBox="0 0 44 22"><path d="M12 3l-8 8 8 8M32 3l8 8-8 8" stroke="#fff" stroke-width="3" fill="none"/></svg></div>
  <p class="quote">" Callvera has opened up a whole new world of measurement for our staff. Their team has been personable, flexible, and focused on improving our bottom line in a way that has made us feel valued as a top priority. We look forward to continuing to work with them on new innovations that can improve both customer and employee satisfaction!.."</p>
  <div class="author-art" role="img" aria-label="Cartoon portrait of the client"></div>
  <div class="author"><strong>MARCO DELVANE</strong>Brightshore</div>
</section>

<section class="section why">
  <div class="why-copy">
    <h2>WHY 3<sup style="font-size:14px">RD</sup> PARTY QA?</h2>
    <p>From call monitoring using dependable human beings to fully integrated web compliance capabilities, our 3rd party QA services provide an unbiased, comprehensive approach to ensure compliance and help maximize customer ex quality assurance services which allows for quick and easy analysis of your call center as a whole, or at the agent level. With an excess of 13 million review minutes logged in just a few short years, we understand that attention to detail is paramount.</p>
    <a class="btn-light" href="#">Learn More</a>
  </div>
  <div class="video">
    <h2>WATCH A VIDEO</h2>
    <div class="video-frame" role="img" aria-label="Video thumbnail: illustration of an agent at a desk ringed by listeners, titled Are You Really Listening">
      <svg class="play" width="80" height="80" viewBox="0 0 80 80"><circle cx="40" cy="40" r="36" fill="none" stroke="#fff" stroke-width="6"/><path d="M32 24l24 16-24 16z" fill="#fff"/></svg>
    </div>
  </div>
</section>

<section class="section cta">
  <div class="cta-brand"><span class="brand-dot"></span><span class="brand-name">Callvera</span></div>
  <div class="cta-copy">
    <h2>WE MEAN BUSINESS</h2>
    <p>Callvera is committed to providing call centers of all shapes and sizes with the essential tools they need to thrive and survive in a world riddled with compliance violations and stagnant agent performance. So if you're as serious as we are about providing the highest quality customer experience possible, take the next step today ..</p>
    <a class="btn-light" href="#">Get In Touch</a>
  </div>
  <div class="contact-row">
    <span><svg width="18" height="26" viewBox="0 0 18 26"><path d="M9 0a9 9 0 0 0-9 9c0 7 9 17 9 17s9-10 9-17a9 9 0 0 0-9-9zm0 12a3 3 0 1 1 0-6 3 3 0 0 1 0 6z" fill="#fff"/></svg>4810 Larkspur Ave Reseda,<br>CA 91335</span>
    <span><svg width="24" height="24" viewBox="0 0 24 24"><path fill="#fff" d="M6.6 10.8a15 15 0 0 0 6.6 6.6l2.2-2.2c.3-.3.7-.4 1-.2 1.1.4 2.3.6 3.6.6.6 0 1 .4 1 1V20c0 .6-.4 1-1 1A17 17 0 0 1 3 4c0-.6.4-1 1-1h3.5c.6 0 1 .4 1 1 0 1.3.2 2.5.6 3.6.1.3 0 .7-.2 1z"/></svg>855.410.2286</span>
    <span><svg width="30" height="22" viewBox="0 0 24 18"><path fill="#fff" d="M0 0h24v18H0zM2 2v1l10 7 10-7V2z"/></svg>hello@callvera.com</span>
  </div>
</section>

<footer class="section site-footer">
  <nav class="footer-nav"><a href="#">HOME</a><a href="#">WHO WE ARE</a><a href="#">SERVICES</a><a href="#">BLOG</a><a href="#">FAQ</a><a href="#">CONTACT</a><a href="#">LOGIN</a></nav>
  <p class="copyright">Copyright © 2017, Company Name<br>All Right Reserved</p>
  <div class="social"><i></i><i></i><i></i><i></i><i></i><i></i></div>
</footer>

</body>
</html>
```